KV HOLDING Business Cards

I need business cards for "KV Holding group LLC" doublesided... logo on the back (also include logo on front)
logo attached to project... i have jpg up..
Company Info:
827 North Cadwell Avenue, Suite 4B
Chicago, Illinois 60654
facsimile 312-481-2075 (list fax, address, website on all cards.)
www.kvholdinggroup.example
Three different people on cards:
Darnell P. Okafor, CPA MST
Principal
ofc 312-481-3900
mobile 312-204-7751
darnellpokafor@kvholdinggroup.example
Hollis T. Brennecke, CPA MST
Principal
hollistbrennecke@kvholdinggroup.example
mobile 708-539-1184
ofc 312-481-3900
Conrad M Pavlik
Principal
ofc 312-481-3900
no mobile
conradmpavlik@kvholdinggroup.example
I have multiple projects listed.. see below:
Business cards for amber gate ventures llc
letterhead
envelopes
Business cards for KV Holding LLC
letterhead
envelopes
Target Market(s)
rich people
Industry/Entity Type
Business
Look and feel
Each slider illustrates characteristics of the customer's brand and the style your logo design should communicate.

```html
<!DOCTYPE html>
<html lang="en">
<head>
<meta charset="utf-8">
<title>KV Holding Group LLC — Business Cards</title>
<link rel="stylesheet" href="https://fonts.googleapis.com/css2?family=Cinzel:wght@500&family=Exo+2:wght@500;600&display=swap">
<style>
  :root {
    --page: #ffffff;
    --navy: #0c3f78;
    --navy-deep: #0d2f55;
    --brand-blue: #1a4b86;
    --band-grey: #8f8f8f;
    --back-grey: #a9a9a9;
    --white: #ffffff;
    --shadow: rgba(0, 0, 0, 0.55);
  }
  * { box-sizing: border-box; margin: 0; padding: 0; }
  html, body { width: 924px; height: 1200px; overflow: hidden; background: var(--page); }
  body { position: relative; font-family: "Exo 2", "Segoe UI", sans-serif; }

  .card { position: absolute; overflow: hidden; box-shadow: 6px 7px 8px var(--shadow); }

  /* Front */
  .card-front { left: 64px; top: 87px; width: 790px; height: 485px; background: var(--white); }
  .front-brand { position: absolute; left: 0; top: 0; width: 397px; height: 485px; }
  .brand-mark { position: absolute; width: 70px; height: 70px; border-radius: 50%; background: var(--brand-blue); }
  .front-brand .brand-mark { left: 163px; top: 205px; }
  .brand-name {
    position: absolute; left: 0; width: 100%; text-align: center;
    font-family: "Cinzel", "Times New Roman", serif; font-weight: 500;
    color: var(--brand-blue); white-space: nowrap;
  }
  .front-brand .brand-name { top: 292px; font-size: 24px; }
  .address-band {
    position: absolute; left: 0; top: 275px; width: 397px; height: 120px;
    background: var(--band-grey); color: var(--white);
    display: flex; flex-direction: column; justify-content: center; align-items: center;
    font-size: 12px; line-height: 17.5px; font-weight: 500; text-align: center;
  }
  .contact-panel { position: absolute; left: 397px; top: 0; width: 393px; height: 485px; background: var(--navy); color: var(--white); text-align: center; }
  .contact-panel .panel-shade { position: absolute; left: 0; top: 275px; width: 100%; height: 120px; background: var(--navy-deep); opacity: 0.75; }
  .person { position: absolute; left: 0; width: 100%; font-weight: 600; white-space: nowrap; }
  .person-okafor { top: 48px; font-size: 16.5px; line-height: 17.5px; }
  .person-brennecke { top: 202px; font-size: 15px; line-height: 16px; }
  .person-pavlik { top: 332px; font-size: 18px; line-height: 20.5px; }

  /* Back */
  .card-back { left: 74px; top: 605px; width: 780px; height: 477px; background: var(--back-grey); }
  .back-field { position: absolute; left: 0; top: 95px; width: 100%; height: 287px; background: var(--white); }
  .back-field .brand-mark { left: 350px; top: 60px; width: 80px; height: 80px; }
  .back-field .brand-name { top: 150px; font-size: 38px; }
</style>
</head>
<body>
  <section class="card card-front" aria-label="Card front">
    <div class="front-brand">
      <span class="brand-mark" aria-hidden="true"></span>
      <p class="brand-name">KV Holding Group LLC</p>
    </div>
    <div class="address-band">
      <p>827 North Cadwell Avenue, Suite 4B</p>
      <p>Chicago, Illinois 60654</p>
      <p>facsimile 312-481-2075 (list fax, address, website on all cards.)</p>
      <p>www.kvholdinggroup.example</p>
    </div>
    <div class="contact-panel">
      <div class="panel-shade"></div>
      <div class="person person-okafor">
        <p>Darnell P. Okafor, CPA MST</p>
        <p>Principal</p>
        <p>Ofc 312-481-3900</p>
        <p>Mobile 312-204-7751</p>
        <p>darnellpokafor@kvholdinggroup.example</p>
      </div>
      <div class="person person-brennecke">
        <p>Hollis T. Brennecke, CPA MST</p>
        <p>Principal</p>
        <p>hollistbrennecke@kvholdinggroup.example</p>
        <p>mobile 708-539-1184</p>
        <p>ofc 312-481-3900</p>
      </div>
      <div class="person person-pavlik">
        <p>Conrad M Pavlik</p>
        <p>Principal</p>
        <p>ofc 312-481-3900</p>
        <p>conradmpavlik@kvholdinggroup.example</p>
      </div>
    </div>
  </section>

  <section class="card card-back" aria-label="Card back">
    <div class="back-field">
      <span class="brand-mark" aria-hidden="true"></span>
      <p class="brand-name">KV Holding Group LLC</p>
    </div>
  </section>
</body>
</html>
```